Business Card Design

New business card design

Target Market(s)

Residential & Commercial Property Managers

Industry/Entity Type

Plumbing Services

Contact Information for Business Card

Name - Rowan Keddle, title - Director, Phone Number - 0431 286 517, email - rowan@tbk-plumbing.com.au, Company ABN - 73 215 904 386,

Font styles to use
Sans Serif

Colors
0054AA
0677BA
7BADD7
CADEEF
E8F1F8

```html
<!DOCTYPE html>
<html lang="en">
<head>
<meta charset="utf-8">
<title>TBK Plumbing Services – Business Card</title>
<link rel="stylesheet" href="https://fonts.googleapis.com/css2?family=Exo+2:wght@400;700;800&display=swap">
<style>
  :root {
    --page-bg: #e9e6e2;
    --card-white: #f7f8f9;
    --card-shade: #e7e9eb;
    --ink-dark: #1b2630;
    --ink-grey: #3a3f44;
    --brand-blue: #2aa6e0;
    --deep-blue: #0677ba;
    --navy: #1d2a35;
    --rule: #8c959c;
  }
  * { margin: 0; padding: 0; box-sizing: border-box; }
  html, body {
    width: 1200px; height: 900px; overflow: hidden;
    background: var(--page-bg);
    font-family: "Exo 2", sans-serif;
  }
  .sheet {
    width: 1200px; height: 900px;
    display: flex; flex-direction: column; align-items: center; justify-content: center;
    gap: 30px;
  }
  .card {
    width: 680px; height: 415px;
    border-radius: 34px;
    position: relative; overflow: hidden;
    box-shadow: 0 10px 24px rgba(0,0,0,.18);
  }
  /* Back side */
  .card--back {
    background: linear-gradient(115deg, #2b93c9 0%, #2a5f7e 45%, var(--navy) 100%);
  }
  .card--back .pattern-area { position: absolute; inset: 0; }
  /* Front side */
  .card--front {
    background: linear-gradient(135deg, var(--card-shade) 0%, var(--card-white) 45%, #ffffff 100%);
    color: var(--ink-grey);
  }
  .holder { position: absolute; left: 40px; top: 96px; }
  .holder__name {
    font-weight: 800; font-size: 27px; color: var(--brand-blue); letter-spacing: .2px;
  }
  .holder__title { font-size: 19px; margin-top: 1px; color: var(--ink-grey); }
  .contact {
    position: absolute; left: 330px; top: 68px;
    font-size: 18px; line-height: 30px; color: var(--ink-grey);
  }
  .contact__row { display: flex; align-items: center; gap: 9px; }
  .contact__icon { width: 17px; height: 17px; flex: none; }
  .contact__label { color: var(--brand-blue); }
  .divider {
    position: absolute; left: 330px; right: 40px; top: 176px;
    border-top: 1px solid var(--rule);
  }
  .brand {
    position: absolute; left: 330px; right: 40px; top: 210px;
    font-size: 44px; font-weight: 400; color: var(--ink-dark);
    letter-spacing: 1px; line-height: 1.1;
  }
</style>
</head>
<body>
<main class="sheet">
  <section class="card card--back" aria-label="Card back">
    <div class="pattern-area" role="img" aria-label="Repeating water drop pattern over a blue to navy gradient"></div>
  </section>

  <section class="card card--front" aria-label="Card front">
    <div class="holder">
      <p class="holder__name">Rowan Keddle</p>
      <p class="holder__title">Director</p>
    </div>

    <div class="contact">
      <p class="contact__row">
        <svg class="contact__icon" viewBox="0 0 24 24" aria-hidden="true"><path fill="var(--deep-blue)" d="M6.6 10.8a15.1 15.1 0 0 0 6.6 6.6l2.2-2.2c.3-.3.7-.4 1-.2 1.1.4 2.3.6 3.6.6.6 0 1 .4 1 1V20c0 .6-.4 1-1 1A17 17 0 0 1 3 4c0-.6.4-1 1-1h3.5c.6 0 1 .4 1 1 0 1.3.2 2.5.6 3.6.1.3 0 .7-.2 1z"/></svg>
        <span>0431 286 517</span>
      </p>
      <p class="contact__row">
        <svg class="contact__icon" viewBox="0 0 24 24" aria-hidden="true"><rect x="2" y="5" width="20" height="14" rx="1.5" fill="var(--deep-blue)"/><path d="M3 6l9 7 9-7" fill="none" stroke="#fff" stroke-width="1.8"/></svg>
        <span>rowan@tbk-plumbing.com.au</span>
      </p>
      <p class="contact__row">
        <span><span class="contact__label">ABN</span> - 73 215 904 386</span>
      </p>
    </div>

    <div class="divider"></div>

    <p class="brand">tbk plumbing services</p>
  </section>
</main>
</body>
</html>
```